Business cards for Norwegian software consultancy business

We are in need of business cards for our Norwegian consultancy company.
“Valto Brindex AS” specializes in software development, architecture and agile methodology, providing mostly on-site services at customers.
The cards should reflect a certain level of business professionalism with an elegant touch, while paying tribute to our modern and technological heritage. Our logo should be featured, as well as room for basic information about the cardholder and legal information of the company (company name, address and VAT number).
We would like our cards to reflect that we are a modern consulting company. It should present a professional image that people will remember. The texture and color pallette should reflect our professionalism and reliability, so we prefer a light color pallette with colors such as gray, white, blue and black. The number of colors used should however not be overwhelming, with the text being distinct and readable.
We are open to untraditional layouts and playful designs as long as they communicate the intent stated above.
You could also take a look at our website http://www.brindex.no for input on our visual profile.
Our logo is attached in the form of vectors and rasterized PNG. Please comment if you would like the black-white and/or inverted versions as well.
Industry/Entity Type
Architecture
Contact Information for Business Card
Company information:
Valto Brindex AS
Kvernlia 14, 3170 Sem
482 71 519
info@brindex.no
www.brindex.no
Employee information:
Full name
Title
Email
Phone
Font styles to use
Look and feel

```html
<!DOCTYPE html>
<html lang="en">
<head>
<meta charset="utf-8">
<title>Valto Brindex AS – Business Cards</title>
<link rel="stylesheet" href="https://fonts.googleapis.com/css2?family=Lato:wght@400;700;900&display=swap">
<style>
  :root {
    --stage: #2b2b2b;
    --card-dark: #3b3b3c;
    --card-light: #f6f6f6;
    --brand-blue: #4a9ad6;
    --ink: #1c1c1c;
    --ink-soft: #b9b9b9;
    --white: #ffffff;
  }
  * { box-sizing: border-box; margin: 0; padding: 0; }
  html, body {
    width: 1200px; height: 873px; overflow: hidden;
    background: var(--stage);
    font-family: "Lato", sans-serif;
  }
  .stage {
    position: relative; width: 1200px; height: 873px;
    display: flex; align-items: center; justify-content: center; gap: 24px;
  }
  .card {
    position: relative; width: 540px; height: 310px;
    border: 6px solid var(--brand-blue);
    overflow: hidden;
  }

  /* Back side */
  .card--back { background: var(--card-dark); }
  .card--back .brand {
    position: absolute; left: 0; right: 0; top: 112px;
    display: flex; align-items: center; justify-content: center; gap: 16px;
  }
  .brand__square {
    width: 34px; height: 34px; background: var(--brand-blue);
  }
  .card--back .brand__name {
    font-weight: 400; font-size: 40px; letter-spacing: 3px; color: var(--white);
  }
  .card--back .tagline {
    position: absolute; left: 0; right: 0; top: 214px; text-align: center;
    font-weight: 700; font-size: 13px; letter-spacing: 5px; color: var(--ink-soft);
  }

  /* Front side */
  .card--front { background: var(--card-light); }
  .card--front .brand {
    position: absolute; left: 150px; top: 38px;
    display: flex; align-items: center; gap: 12px;
  }
  .card--front .brand__square { width: 24px; height: 24px; }
  .card--front .brand__name {
    font-weight: 400; font-size: 28px; letter-spacing: 2px; color: var(--ink);
  }
  .holder {
    position: absolute; right: 0; top: 112px; text-align: right;
  }
  .holder__name {
    display: inline-block; background: var(--brand-blue); color: var(--white);
    font-weight: 900; font-size: 16px; padding: 5px 22px 5px 18px;
    border-radius: 14px 0 0 14px;
  }
  .holder__title {
    font-size: 13px; color: var(--ink); padding: 4px 22px 0 0;
  }
  .icon-rail {
    position: absolute; left: 0; top: 164px; width: 28px; height: 108px;
    background: var(--brand-blue); border-radius: 0 10px 10px 0;
    display: flex; flex-direction: column; align-items: center; justify-content: space-around;
    padding: 6px 0;
  }
  .icon-rail svg { width: 14px; height: 14px; }
  .contacts {
    position: absolute; left: 46px; top: 166px; list-style: none;
  }
  .contacts li {
    font-weight: 700; font-size: 14px; color: var(--ink); height: 26px; line-height: 26px;
  }
  .footer-band {
    position: absolute; left: 0; bottom: 0; width: 528px; height: 56px;
  }
  .footer-band__company {
    position: absolute; left: 170px; bottom: 7px;
    font-weight: 700; font-size: 17px; letter-spacing: .5px; color: var(--white);
  }
  .footer-band__vat {
    position: absolute; right: 22px; bottom: 31px;
    font-weight: 700; font-size: 12px; letter-spacing: .5px; color: var(--white);
  }
</style>
</head>
<body>
<main class="stage">

  <section class="card card--back" aria-label="Card back">
    <div class="brand">
      <span class="brand__square"></span>
      <span class="brand__name">VALTO BRINDEX</span>
    </div>
    <p class="tagline">DEVELOPMENT &amp; IT SERVICES</p>
  </section>

  <section class="card card--front" aria-label="Card front">
    <div class="brand">
      <span class="brand__square"></span>
      <span class="brand__name">VALTO BRINDEX</span>
    </div>

    <div class="holder">
      <span class="holder__name">Henrik Solvang</span>
      <p class="holder__title">Owner / Founder</p>
    </div>

    <div class="icon-rail">
      <svg viewBox="0 0 14 14" aria-label="Phone"><rect x="3.5" y="1" width="7" height="12" rx="1.2" fill="none" stroke="#fff" stroke-width="1.4"/><line x1="6" y1="11" x2="8" y2="11" stroke="#fff" stroke-width="1.2"/></svg>
      <svg viewBox="0 0 14 14" aria-label="Email"><rect x="1" y="3" width="12" height="8.5" fill="#fff"/><path d="M1 3 L7 8 L13 3" fill="none" stroke="#4a9ad6" stroke-width="1.2"/></svg>
      <svg viewBox="0 0 14 14" aria-label="Website"><rect x="1.5" y="5.5" width="6" height="3" rx="1.5" transform="rotate(-45 4.5 7)" fill="none" stroke="#fff" stroke-width="1.4"/><rect x="6.5" y="5.5" width="6" height="3" rx="1.5" transform="rotate(-45 9.5 7)" fill="none" stroke="#fff" stroke-width="1.4"/></svg>
      <svg viewBox="0 0 14 14" aria-label="Address"><path d="M7 13 C3 8.5 2.5 7 2.5 5.5 A4.5 4.5 0 0 1 11.5 5.5 C11.5 7 11 8.5 7 13Z" fill="#fff"/><circle cx="7" cy="5.5" r="1.7" fill="#4a9ad6"/></svg>
    </div>

    <ul class="contacts">
      <li>+47 482 71 519</li>
      <li>info@brindex.no</li>
      <li>www.brindex.no</li>
      <li>Kvernlia 14, 3170 Sem, Norway</li>
    </ul>

    <div class="footer-band">
      <svg width="528" height="56" viewBox="0 0 528 56" aria-hidden="true">
        <path d="M150 56 L150 38 Q150 32 156 32 L350 32 Q356 32 358 26 L362 10 Q364 4 370 4 L516 4 Q528 4 528 16 L528 56 Z" fill="var(--brand-blue)"/>
      </svg>
      <span class="footer-band__company">VALTO BRINDEX AS</span>
      <span class="footer-band__vat">VAT 917 452 308</span>
    </div>
  </section>

</main>
</body>
</html>
```